Local Chiropractoc needs Modern Website

This website needs to have an upscale look with a very modern feel.

This is for a home page psd layout and an interior page psd file so 2 files total

Below is the information and websites to reference

Add Logo that is attached.

Build a color scheme similar to this website image titled "chiro-1" using the golds, whites, blacks and browns from the color of the logo

I want to see a light background so it makes the images and logo stick out

Must Include these pages in a horizontal menu bar in this order:
Home, Why Fair Ridge?, How Chiropractic Helps, Ask the Doctor, Work Place Wellness, Request an Appointment, Blog, Contact Us

Please add the following social media logos to the top and footer of the website: Chatterly, Plexo+, Vidzio

Build a "classy looking" Make An Appointment Button into the header with the contact info below

Phone Number:
555-014-2297

Address:
4172 North Maple Blvd, Suite #7
Cedar Point, FL 34021

This website needs 4 rotating banners. Please reference a layout similar to this for the banners: http://hollowpinespine.com/. However design it nicer than this website

Below are the description for each banner

Rotating Banner #1
Use Image: Patients are Saying
Add a line of text: "What our Patients are Saying"

Rotating Banner #2
Use Image: Becoming a Patient
Add a line of text: "Interested in Becoming a Patient"

Rotating Banner #3
Use Image: Dinner with Doctor
Add a line of text: "Win A free Dinner with Dr. Hollins"

Rotating Banner #4
Use Image: Chatterly
Add a line of text: Follow us on Chatterly
Bullet point these 4 lines underneath the "Follow us on Chatterly" text:
- Cutting Edge Health News
- Healthy Recipes
- Newest Health Products
- Clinic Events

I'd like to see a free consultation box similar to the "chiro-1" image. Fields to include are: First Name, Last Name, Phone Number, Comments

For the body, please fill it with latin text. Please design a professional 2 column layout similar to the www.hollowpinespine.com website. (DO NOT COPY THIS WEBSITE, USE IT AS REFERENCE)

In the left column include in this order:
Video
Rate us on Plexo Button, Find us on Chatterly Button
Welcome Letter

In the right column include this:

Office Hours
Monday: 8:00-11:00, 2:00-5:00
Tuesday: 8:30-11:00, 2:00-5:30
Wednesday: 8:00-11:00, 2:00-5:00
Thursday: 10:00-12:00, 2:30-5:00
Friday: 8:00-10:00, 1:00-5:00
Saturday: Closed
Sunday: Closed

Patient Testimonials
Fill with a latin text testimonial. This spot will rotate different testimonials

For the footer please design something similar to the layout of this: http://www.tidewellhealer.com/

Also include in the Footer: Powered by Crestline Pixel Group

```html
<!DOCTYPE html>
<html lang="en">
<head>
<meta charset="utf-8">
<title>Fair Ridge Chiropractic</title>
<link href="https://fonts.googleapis.com/css2?family=Signika:wght@400;600;700&family=PT+Sans:ital,wght@0,400;0,700;1,400&display=swap" rel="stylesheet">
<style>
:root{
  --gold:#b89a5a;
  --gold-dark:#9c8049;
  --ink:#2d2d2d;
  --ink-soft:#3a3a3a;
  --page:#f1eee8;
  --card:#ffffff;
  --text:#666;
  --line:#e6e2d9;
  --row:#f4f4f4;
}
*{box-sizing:border-box;margin:0;padding:0}
html,body{width:912px;height:1200px;overflow:hidden}
body{background:var(--page);font-family:"PT Sans",sans-serif;color:var(--text);position:relative}
.abs{position:absolute}
/* header */
.logo{left:122px;top:58px;width:240px;height:60px;white-space:nowrap}
.logo .name{font-family:"Signika",sans-serif;font-weight:700;font-size:30px;color:var(--ink);line-height:30px;display:block;margin-left:32px}
.logo .sub{font-family:"Signika",sans-serif;font-weight:600;font-size:15px;color:var(--gold);letter-spacing:1.2px;display:block;margin-left:32px;margin-top:4px}
.logo .mark{position:absolute;left:0;top:6px;width:22px;height:22px;background:var(--ink)}
.social{display:flex;gap:4px}
.social span{width:20px;height:20px;border-radius:50%;border:1px solid var(--gold);color:var(--gold);font:700 9px/18px "Signika",sans-serif;text-align:center}
.social span.on{background:var(--gold);color:#fff}
.top-social{left:740px;top:57px}
.contact-bar{left:393px;top:88px;width:290px;height:35px;background:var(--ink);display:flex;align-items:center;color:#fff;font-size:8px;white-space:nowrap}
.contact-bar .item{display:flex;align-items:center;gap:8px;padding:0 10px;height:100%}
.contact-bar .item+.item{border-left:1px solid #444}
.contact-bar b{display:block;font-family:"Signika",sans-serif;font-size:8.5px}
.contact-bar i{color:#999;font-size:7.5px}
.appt{left:676px;top:88px;width:131px;height:35px;background:var(--gold);color:#fff;font:600 8.5px/35px "Signika",sans-serif;text-align:right;padding-right:12px;clip-path:polygon(8px 0,100% 0,100% 100%,8px 100%,0 50%)}
/* nav */
.nav{left:105px;top:137px;width:702px;height:46px;background:var(--ink);display:flex}
.nav a{flex:1 1 auto;text-align:center;color:#fff;font:400 7.5px/46px "Signika",sans-serif;padding:0 8px;text-decoration:none;border-right:1px solid #3d3d3d;text-transform:uppercase;white-space:nowrap}
.nav a:last-child{border-right:0}
.nav a.active{background:var(--gold)}
/* banner */
.banner{left:105px;top:194px;width:702px;height:228px;overflow:hidden}
.banner .photo{position:absolute;left:0;top:0;width:100%;height:100%;background:linear-gradient(120deg,#e6dccb,#f0d9b6 45%,#d98a35 80%,#8aa043)}
.banner .panel{position:absolute;right:0;top:0;width:240px;height:100%;background:var(--gold);border-top-left-radius:40px 120px;border-bottom-left-radius:30px 110px;color:#fff;padding:46px 0 0 50px}
.panel h2{font:600 16px/21px "Signika",sans-serif}
.panel ul{list-style:none;margin-top:12px;font-style:italic;font-size:7.5px;line-height:17px}
.dots{display:flex;gap:3px}
.dots span{width:6px;height:6px;border-radius:50%;background:rgba(255,255,255,.4)}
.dots span.on{background:#fff}
.consult{position:absolute;left:0;top:0;width:154px;height:100%;background:rgba(70,60,50,.72);padding:8px 12px;color:#fff}
.consult small{font-size:7px;display:block;padding-left:16px}
.consult strong{font:600 10px "Signika",sans-serif;display:block;margin-top:2px;padding-left:16px}
.consult em{display:block;font-size:7.5px;font-weight:700;text-align:center;margin:26px 0 8px}
.field{border:1px solid rgba(255,255,255,.7);border-radius:2px;height:19px;margin-bottom:5px;font-size:7px;font-style:italic;padding:4px 10px}
.field.fill{background:rgba(255,255,255,.25)}
.field.tall{height:45px}
.submit{display:inline-block;background:var(--gold);font:600 7px/22px "Signika",sans-serif;padding:0 12px;border-radius:2px;margin-top:3px}
/* content */
.card{left:105px;top:433px;width:702px;height:653px;background:var(--card);border:1px solid var(--line)}
.heading{font:600 10px "Signika",sans-serif;color:var(--ink);display:flex;align-items:center;gap:6px;text-transform:uppercase;white-space:nowrap}
.heading::before{content:"";width:2px;height:9px;background:var(--gold)}
.heading::after{content:"";flex:1;height:5px;background:#f3f1ec}
.video{left:123px;top:493px;width:438px;height:227px;border:1px solid var(--line);padding:6px}
.video .frame{width:100%;height:191px;background:linear-gradient(160deg,#c9d3cf,#b8c4a6 50%,#7d9a58)}
.video .bar{height:22px;background:#222;display:flex;align-items:center;color:#888;font-size:6px;gap:8px;padding:0 8px}
.video .track{flex:1;height:2px;background:#555;position:relative}
.video .track::before{content:"";position:absolute;left:0;top:0;width:35%;height:2px;background:var(--gold)}
.play{left:327px;top:594px;width:28px;height:28px;background:rgba(255,255,255,.5);border-radius:3px}
.sbtn{height:46px;background:var(--ink);display:flex;border-bottom:2px solid var(--gold)}
.sbtn .ic{width:46px;background:var(--gold);display:flex;align-items:center;justify-content:center}
.sbtn .ic span{width:14px;height:14px;border-radius:50%;border:2px solid #fff}
.sbtn .t{padding:8px 0 0 40px;color:#fff;font:600 7px "Signika",sans-serif}
.sbtn .t b{display:block;color:var(--gold);font-size:20px;line-height:22px;letter-spacing:.5px}
.hours{left:578px;top:468px;width:211px;height:194px;border:1px solid var(--line)}
.hours h3{background:var(--gold);color:#fff;font:600 10px/34px "Signika",sans-serif;text-align:center}
.hours table{width:100%;border-collapse:collapse;font-size:7px}
.hours td{height:22.8px;padding:0 10px;color:#777}
.hours td:first-child{color:var(--ink);font-weight:700}
.hours td:last-child{text-align:right}
.hours tr:nth-child(odd){background:var(--row)}
.hours tr.closed td{color:var(--gold)}
.testi{left:578px;top:716px;width:211px;height:103px;background:#f0f0f0}
.testi p{font-style:italic;font-size:7.5px;line-height:14.5px;color:#888;padding:14px 20px 0 20px;text-indent:30px}
.testi .q{position:absolute;left:18px;top:12px;font:700 40px/30px "Signika",sans-serif;color:#ddd}
.testi .who{position:absolute;left:0;bottom:0;width:100%;height:23px;background:var(--gold);color:#fff;font:600 7px/23px "Signika",sans-serif;padding-left:16px}
.testi .who .dots{position:absolute;right:12px;top:8px}
.divider{left:105px;top:854px;width:702px;height:1px;background:#f0eee9}
.letter{left:123px;top:913px;width:325px;font-size:7.7px;line-height:15px;text-align:justify}
.family{left:465px;top:912px;width:324px;height:140px;background:linear-gradient(135deg,#9fbf6e,#e6c2a8 45%,#c7d7e6 75%,#7ea24f)}
/* footer */
.foot-links{left:0;top:1086px;width:912px;height:57px;background:var(--gold)}
.foot-links nav{position:absolute;left:122px;top:22px;font:600 7.5px "Signika",sans-serif;color:#fff;display:flex;gap:5px;white-space:nowrap}
.foot-links .brand{position:absolute;left:720px;top:14px;color:#fff;font:700 13px/13px "Signika",sans-serif}
.foot-links .brand small{display:block;font-size:6.5px;letter-spacing:.6px}
.foot-base{left:0;top:1143px;width:912px;height:57px;background:var(--ink);color:#fff;font:600 7.5px/10px "Signika",sans-serif}
.foot-base .addr{position:absolute;left:122px;top:20px;text-align:center}
.foot-base .addr i,.foot-base .copy i{font-weight:400}
.foot-base .copy{position:absolute;right:122px;top:20px;text-align:right}
.foot-base .copy em{color:var(--gold)}
.foot-base .social{position:absolute;left:415px;top:17px;gap:8px}
.foot-base .social span{border-radius:2px;width:22px;height:22px;line-height:20px}
</style>
</head>
<body>

<header>
  <div class="abs logo"><span class="mark"></span><span class="name">FAIR RIDGE</span><span class="sub">CHIROPRACTIC</span></div>
  <div class="abs social top-social"><span aria-label="Chatterly">C</span><span class="on" aria-label="Plexo+">P</span><span aria-label="Vidzio">V</span></div>
  <div class="abs contact-bar">
    <div class="item">
      <svg width="14" height="14" viewBox="0 0 24 24"><path fill="#b89a5a" d="M6.6 10.8a15 15 0 006.6 6.6l2.2-2.2c.3-.3.7-.4 1-.2 1.1.4 2.3.6 3.6.6.6 0 1 .4 1 1V20c0 .6-.4 1-1 1A17 17 0 013 4c0-.6.4-1 1-1h3.5c.6 0 1 .4 1 1 0 1.3.2 2.5.6 3.6.1.3 0 .7-.2 1z"/></svg>
      <div><b>555-014-2297</b><i>hello@fairridgechiro.com</i></div>
    </div>
    <div class="item">
      <svg width="16" height="14" viewBox="0 0 24 20"><path fill="#b89a5a" d="M12 0L0 10h3v10h7v-6h4v6h7V10h3z"/></svg>
      <div><b>4172 North Maple Blvd, Suite #7</b><i>Cedar Point, FL 34021</i></div>
    </div>
  </div>
  <div class="abs appt">MAKE AN APPOINTMENT</div>
  <nav class="abs nav">
    <a>Home</a><a class="active">Why Fair Ridge?</a><a>How Chiropractic Helps</a><a>Ask the Doctor</a><a>Work Place Wellness</a><a>Request an Appointment</a><a>Blog</a><a>Contact Us</a>
  </nav>
</header>

<section class="abs banner">
  <div class="photo" role="img" aria-label="Smiling baby flexing an arm beside orange juice, carrots and fruit"></div>
  <div class="consult">
    <small>CONTACT US NOW &amp; GET YOUR</small>
    <strong>FREE CONSULTATION</strong>
    <em>WELLNESS BEGINS HERE</em>
    <div class="field">First Name</div>
    <div class="field fill">Last Name</div>
    <div class="field">Phone Number</div>
    <div class="field tall">Comments ...</div>
    <div class="submit">Submit ➜</div>
  </div>
  <div class="panel">
    <h2>Follow Us on<br>Chatterly</h2>
    <ul><li>- Cutting Edge Health News</li><li>- Healthy Recipes</li><li>- Newest Health Products</li><li>- Clinic Events</li></ul>
    <div class="dots" style="margin-top:48px"><span></span><span class="on"></span><span></span><span></span></div>
  </div>
</section>

<main>
  <div class="abs card"></div>
  <h2 class="abs heading" style="left:123px;top:466px;width:438px">Our Videos</h2>
  <div class="abs video">
    <div class="frame" role="img" aria-label="Video still of a smiling family of three generations outdoors"></div>
    <div class="bar"><span>▶</span><span>00:28</span><div class="track"></div><span>02:36</span><span>◀)</span></div>
  </div>
  <div class="abs play"><svg width="28" height="28"><path d="M11 9l8 5-8 5z" fill="#555"/></svg></div>

  <h2 class="abs heading" style="left:123px;top:747px;width:438px">We're on Social Medias</h2>
  <div class="abs sbtn" style="left:123px;top:773px;width:210px"><div class="ic"><span></span></div><div class="t">RATE US ON<b>PLEXO</b></div></div>
  <div class="abs sbtn" style="left:351px;top:773px;width:210px"><div class="ic"><span></span></div><div class="t">FIND US ON<b>CHATTERLY</b></div></div>

  <div class="abs hours">
    <h3>OFFICE HOURS</h3>
    <table>
      <tr><td>Monday</td><td>8:00-11:00 AM, 2:00-5:00 PM</td></tr>
      <tr><td>Tuesday</td><td>8:30-11:00 AM, 2:00-5:30 PM</td></tr>
      <tr><td>Wednesday</td><td>8:00-11:00 AM, 2:00-5:00 PM</td></tr>
      <tr><td>Thursday</td><td>10:00-12:00 AM, 2:30-5:00 PM</td></tr>
      <tr><td>Friday</td><td>8:00-10:00 AM, 1:00-5:00 PM</td></tr>
      <tr class="closed"><td>Saturday</td><td>Closed</td></tr>
      <tr class="closed"><td>Sunday</td><td>Closed</td></tr>
    </table>
  </div>

  <h2 class="abs heading" style="left:578px;top:689px;width:211px">Patient Testimonials</h2>
  <div class="abs testi">
    <span class="q">“</span>
    <p>Pellentesque habitant morbi tristique senectus et netus et malesuada fames ac turpis egestas. Donec faucibus aliquet dui, nec congue orci sagittis eget.</p>
    <div class="who">- Mr. Daniel Ashford -<div class="dots"><span></span><span class="on"></span><span></span><span></span></div></div>
  </div>

  <div class="abs divider"></div>
  <h2 class="abs heading" style="left:123px;top:887px;width:666px">Welcome Letter</h2>
  <p class="abs letter">Hello Dear Visitor,<br>Vestibulum malesuada tortor volutpat risus finibus, in consequat nibh dictum. Pellentesque vestibulum nisi nisl, vel accumsan dui consequat sed. Integer non justo et mi interdum pretium. Proin ut pulvinar eros. Pellentesque at luctus odio, a ullamcorper urna. Nam semper feugiat massa non pulvinar. Curabitur sagittis, odio eget posuere ultricies, sem nisi pulvinar turpis, at laoreet arcu neque lacinia odio. Nulla nec nunc ac felis auctor fermentum quis ut justo. Donec ultricies feugiat accumsan. Integer leo justo, dapibus id mauris quis, vestibulum rutrum arcu. Etiam sed ipsum eu augue condimentum ullamcorper vel ac sapien. Cras sed lorem et est interdum commodo vitae sit amet orci. Ut mattis tempor metus sed venenatis.</p>
  <div class="abs family" role="img" aria-label="Happy family of four embracing in a sunny park"></div>
</main>

<footer>
  <div class="abs foot-links">
    <nav><span>Home</span>|<span>Why Fair Ridge?</span>|<span>How Chiropractic Helps</span>|<span>Ask the Doctor</span>|<span>Work Place Wellness</span>|<span>Request an Appointment</span>|<span>Blog</span>|<span>Contact Us</span></nav>
    <div class="brand">FAIR RIDGE<small>CHIROPRACTIC</small></div>
  </div>
  <div class="abs foot-base">
    <div class="addr">4172 North Maple Blvd, Suite #7<br><i>Cedar Point, FL 34021</i></div>
    <div class="social"><span aria-label="Chatterly">C</span><span class="on" aria-label="Plexo+">P</span><span aria-label="Vidzio">V</span></div>
    <div class="copy">Copyright © 2015, Fair Ridge Chiropractic<br><i>Powered by</i> <em>Crestline Pixel Group</em></div>
  </div>
</footer>

</body>
</html>
```